Venture Capital Investment Firm

We are looking to overhaul our existing website (substantially), with only using the same logos (which we can provide).
We are an investment firm that focuses on making loans to late stage technology companies. Our site should ultimately look like other venture capital firms, and look modern and fresh. We have an existing website www.norvellhub.com which this will be replacing, although we will be using a lot of the existing written content, and potentially the numbers of pages we will need, we are not wed to anything else. Please feel free to shoot any questions at any time and thank you in advance for your help!
Websites we like as examples:
https://www.tesmarkfund.com/
https://www.brindlewoodpartners.com/
Target Market(s)
Potential investors who will invest in our firm, as well as potentially companies that are looking to borrow money from us.
Coding
Coded - Design and coding required
Number of Pages Required
5+ page
Colors
Designer to choose colors to be used in the design.
Look and feel

```html
<!DOCTYPE html>
<html lang="en">
<head>
<meta charset="utf-8">
<title>Norvell Hub — Investment Partners</title>
<link href="https://fonts.googleapis.com/css2?family=Poppins:wght@400;500;600&family=Lato:wght@400;700&display=swap" rel="stylesheet">
<style>
:root{
  --navy:#221c44;
  --navy-deep:#15122e;
  --ink:#1d1d1f;
  --body:#555;
  --grey-band:#6e6d72;
  --line:#e2e2e2;
  --footer:#3a3a3c;
  --white:#fff;
}
*{box-sizing:border-box;margin:0;padding:0}
html,body{width:1200px;height:3747px;overflow:hidden}
body{position:relative;background:var(--white);font-family:"Lato",sans-serif;color:var(--body)}
.abs{position:absolute}
.ph{position:absolute;display:block}

/* header */
.site-header{position:absolute;left:0;top:0;width:1200px;height:114px;background:var(--white)}
.brand{position:absolute;left:109px;top:28px;display:flex;align-items:center;gap:14px}
.brand-mark{width:42px;height:42px;border-radius:50%;background:var(--navy)}
.brand-name{font-family:"Poppins",sans-serif;font-weight:500;font-size:30px;color:var(--navy);line-height:1;letter-spacing:.5px}
.nav{position:absolute;top:54px;left:462px;display:flex;gap:28px;font-family:"Poppins",sans-serif;font-size:14.5px;color:#333;letter-spacing:.3px}
.nav .active{position:relative}
.nav .active::after{content:"";position:absolute;left:5px;right:5px;bottom:-10px;height:2px;background:var(--ink)}
.btn-investors{position:absolute;left:990px;top:45px;width:98px;height:39px;background:var(--navy);color:#fff;border-radius:5px;font-family:"Poppins",sans-serif;font-size:14px;font-weight:500;display:flex;align-items:center;justify-content:center}

/* hero */
.hero{position:absolute;left:0;top:115px;width:1200px;height:515px;background:linear-gradient(120deg,#6f7471 0%,#a9aaa4 35%,#cfd0cb 55%,#8f948f 100%)}
.hero-panel{position:absolute;left:371px;top:186px;width:497px;height:207px;background:rgba(40,40,50,.55);text-align:center;color:#fff}
.hero-panel h1{font-family:"Poppins",sans-serif;font-weight:600;font-size:60px;letter-spacing:2px;margin-top:8px;line-height:1.1}
.hero-panel p{font-size:14.5px;line-height:24px;width:440px;margin:0 auto}
.btn-start{position:absolute;left:160px;top:135px;width:145px;height:47px;background:var(--navy);color:#fff;font-family:"Poppins",sans-serif;font-size:14px;font-weight:500;border-radius:3px;display:flex;align-items:center;justify-content:center}
.hero-arrow{position:absolute;top:247px}

/* section heads */
.section-title{position:absolute;left:0;width:1200px;text-align:center;font-family:"Poppins",sans-serif;font-weight:500;font-size:30px;color:var(--ink);letter-spacing:1.5px}
.title-rule{position:absolute;left:568px;width:64px;height:3px;background:var(--navy)}

/* about */
.about-title{left:110px;top:722px;font-family:"Poppins",sans-serif;font-weight:500;font-size:29px;color:var(--ink);letter-spacing:1px}
.about-text{left:112px;top:793px;width:522px;font-size:14.8px;line-height:26.6px;text-align:justify;color:#5a5a5a}
.btn-outline{position:absolute;display:flex;align-items:center;justify-content:center;font-family:"Poppins",sans-serif;font-size:14px;font-weight:500;border-radius:6px}
.about-more{left:110px;top:1077px;width:114px;height:44px;border:2px solid var(--ink);color:var(--ink)}
.about-shadow{left:673px;top:785px;width:412px;height:307px;background:var(--navy-deep)}
.about-photo{left:662px;top:772px;width:411px;height:306px;background:linear-gradient(180deg,#e9b25a 0%,#f3d99a 40%,#c9c1a6 75%,#8f8a7a 100%);border-radius:3px;box-shadow:0 4px 14px rgba(0,0,0,.25)}

/* services */
.service-dark{left:0;top:1305px;width:579px;height:440px;background:var(--navy)}
.service-grey{left:579px;top:1745px;width:621px;height:440px;background:var(--grey-band)}
.svc-title{position:absolute;font-family:"Poppins",sans-serif;font-weight:500;font-size:19.5px;color:#fff;letter-spacing:.3px}
.svc-rule{position:absolute;width:46px;height:2px;background:#fff}
.svc-text{position:absolute;width:444px;font-size:14.6px;line-height:25.8px;text-align:justify;color:#dcdbe4}
.svc-btn{position:absolute;height:43px;width:137px;border:2px solid #fff;color:#fff;font-family:"Poppins",sans-serif;font-size:14px;font-weight:500;display:flex;align-items:center;justify-content:center}
.svc-btn.dark{border-color:var(--navy)}

/* news */
.news-card{position:absolute;top:2372px;width:320px;height:428px;border:1px solid var(--line);background:#fff}
.news-img{position:absolute;left:14px;top:14px;width:291px;height:177px}
.news-title{position:absolute;left:14px;top:217px;width:292px;font-family:"Poppins",sans-serif;font-size:14.3px;line-height:25px;color:var(--ink);letter-spacing:.2px}
.news-text{position:absolute;left:14px;top:283px;width:292px;font-size:15.5px;line-height:24px;color:#555;text-align:justify}
.news-rule{position:absolute;left:14px;top:363px;width:60px;height:3px;background:var(--navy)}
.news-meta{position:absolute;left:14px;top:388px;display:flex;align-items:center;gap:8px;font-family:"Poppins",sans-serif;font-size:13px;color:#555}
.news-arrow{position:absolute;top:2512px;width:40px;height:40px;border-radius:50%;border:1px solid #bbb;background:#fff;display:flex;align-items:center;justify-content:center}

/* cta */
.cta{left:0;top:2902px;width:1200px;height:196px;background:linear-gradient(90deg,#2c2a33,#4c4649 50%,#2d2b36)}
.cta-text{position:absolute;left:190px;top:80px;font-family:"Poppins",sans-serif;font-size:29px;color:#fff;letter-spacing:1px}
.cta-btn{position:absolute;left:807px;top:73px;width:198px;height:51px;background:#fff;border-radius:4px;color:var(--ink);font-family:"Poppins",sans-serif;font-size:14px;font-weight:500;display:flex;align-items:center;justify-content:center}

/* team */
.member{position:absolute;top:3280px;width:260px;text-align:center}
.avatar{width:192px;height:192px;border-radius:50%;margin:0 auto;background:radial-gradient(circle at 50% 40%,#8a8a8a,#2c2c2c 70%)}
.avatar.hover{background:var(--navy);display:flex;flex-direction:column;align-items:center;justify-content:center;color:#fff;padding:0 28px}
.avatar.hover strong{font-family:"Poppins",sans-serif;font-weight:500;font-size:14.5px;margin-bottom:6px}
.avatar.hover span{font-family:"Poppins",sans-serif;font-size:12px;line-height:20px}
.member-name{margin-top:26px;font-family:"Poppins",sans-serif;font-size:15px;font-weight:500;color:var(--ink)}
.member-role{margin-top:11px;font-family:"Poppins",sans-serif;font-size:14.5px;color:var(--ink)}

/* footer */
.site-footer{left:0;top:3639px;width:1200px;height:108px;background:var(--footer)}
.footer-nav{position:absolute;left:109px;top:41px;display:flex;gap:23px;font-family:"Poppins",sans-serif;font-size:15px;color:#fff}
.copyright{position:absolute;right:112px;top:41px;font-family:"Poppins",sans-serif;font-size:15px;color:#fff}
</style>
</head>
<body>

<header class="site-header">
  <div class="brand"><span class="brand-mark"></span><span class="brand-name">Norvell Hub</span></div>
  <nav class="nav">
    <span class="active">HOME</span><span>STRATEGY</span><span>ABOUT US</span><span>TEAM</span><span>NEWS</span><span>CONTACT</span>
  </nav>
  <div class="btn-investors">INVESTORS</div>
</header>

<section class="hero" role="img" aria-label="Business team meeting around a table with charts">
  <svg class="hero-arrow" style="left:70px" width="12" height="22" viewBox="0 0 12 22"><path d="M10 2 2 11l8 9" fill="none" stroke="#222" stroke-width="1.6"/></svg>
  <svg class="hero-arrow" style="left:1116px" width="12" height="22" viewBox="0 0 12 22"><path d="M2 2l8 9-8 9" fill="none" stroke="#222" stroke-width="1.6"/></svg>
  <div class="hero-panel">
    <h1>NORVELL HUB</h1>
    <p>Our focus spans the life science and technology industries, two sectors where intellectual property (IP)</p>
    <div class="btn-start">GET STARTED</div>
  </div>
</section>

<h2 class="abs about-title">ABOUT US</h2>
<p class="abs about-text">Norvell Hub is a private investment firm unique in its dual focus on life science and technology credit opportunities. Our ambidextrous approach to investing reflects a broad recognition and appreciation for the critical role intellectual property plays in the successful commercialization of products. We apply our extensive industry expertise to assess the revenue visibility created by these assets and offer a range of creative financing solutions.pioneer in providing life science structured credit beginning in 2004, the Norvell Hub team was the first to introduce flexible structured credit to the technology sector in 2014. Our team was also early to recognize the potential of “non-core” assets beyond drug royalties,</p>
<div class="btn-outline about-more">READ MORE</div>
<div class="ph about-shadow"></div>
<div class="ph about-photo" role="img" aria-label="Coins dropping into jars with growing plants at sunset"></div>

<h2 class="section-title" style="top:1213px">OUR SERVICES</h2>
<div class="title-rule" style="top:1261px"></div>

<section class="ph service-dark">
  <h3 class="svc-title" style="left:110px;top:52px">HEALTHCARE</h3>
  <div class="svc-rule" style="left:110px;top:93px"></div>
  <p class="svc-text" style="left:110px;top:112px">Sed ut perspiciatis unde omnis iste natus error sit voluptatem accusantium doloremque laudantium, totam rem aperiam, eaque ipsa quae ab illo inventore veritatis et quasi architecto beatae vitae dicta sunt explicabo. Nemo enim ipsam voluptatem quia voluptas sit aspernatur aut odit aut fugit, sed quia consequuntur magni dolores eos qui ratione voluptatem sequi nesciunt. Neque porro quisquam est, qui dolorem ipsum quia dolor sit amet, consectetur, adipisci velit,</p>
  <div class="svc-btn" style="left:112px;top:334px">READ MORE</div>
</section>
<div class="ph" style="left:579px;top:1305px;width:621px;height:440px;background:linear-gradient(110deg,#e8ecef,#c9d3dc 45%,#eef1f3)" role="img" aria-label="Smiling businessman and nurse in scrubs with a clipboard"></div>

<div class="ph" style="left:0;top:1745px;width:579px;height:440px;background:linear-gradient(135deg,#d9dde0,#9aa1a6 55%,#eceeef)" role="img" aria-label="Colleagues reviewing financial charts on a laptop and papers"></div>
<section class="ph service-grey">
  <h3 class="svc-title" style="left:86px;top:50px">TECHNOLOGY INDUSTRIES</h3>
  <div class="svc-rule" style="left:86px;top:91px"></div>
  <p class="svc-text" style="left:86px;top:110px;width:443px">Sed ut perspiciatis unde omnis iste natus error sit voluptatem accusantium doloremque laudantium, totam rem aperiam, eaque ipsa quae ab illo inventore veritatis et quasi architecto beatae vitae dicta sunt explicabo. Nemo enim ipsam voluptatem quia voluptas sit aspernatur aut odit aut fugit, sed quia consequuntur magni dolores eos qui ratione voluptatem sequi nesciunt. Neque porro quisquam est, qui dolorem ipsum quia dolor sit amet, consectetur, adipisci velit,</p>
  <div class="svc-btn dark" style="left:87px;top:334px">READ MORE</div>
</section>

<h2 class="section-title" style="top:2278px">NORVELL HUB NEWS</h2>
<div class="title-rule" style="top:2328px"></div>

<div class="news-arrow" style="left:22px"><svg width="10" height="14" viewBox="0 0 10 14"><path d="M7 2 2 7l5 5" fill="none" stroke="#333" stroke-width="1.4"/></svg></div>
<div class="news-arrow" style="left:1129px"><svg width="10" height="14" viewBox="0 0 10 14"><path d="M3 2l5 5-5 5" fill="none" stroke="#333" stroke-width="1.4"/></svg></div>

<article class="news-card" style="left:110px">
  <div class="news-img" style="background:linear-gradient(135deg,#dfe6ee,#3c5a85 60%,#1f2f4d)" role="img" aria-label="Two businessmen shaking hands"></div>
  <h4 class="news-title">NORVELL HUB COMPLETES STRUCTURED DEBT INVESTMENT IN BRIGHTLANE</h4>
  <p class="news-text">Brightlane sustain our momentum and scale our employee communication solutions to meet the growing</p>
  <div class="news-rule"></div>
  <div class="news-meta"><svg width="12" height="12"><rect x="1" y="2" width="10" height="9" fill="none" stroke="#888"/><rect x="1" y="2" width="10" height="3" fill="#888"/></svg>APRIL 30, 2018 &nbsp;&nbsp; <svg width="14" height="12"><path d="M2 10l10-8M4 11l9-7" stroke="#888" fill="none"/></svg>15</div>
</article>
<article class="news-card" style="left:438px">
  <div class="news-img" style="background:linear-gradient(135deg,#5a7a2a,#b6a64a 55%,#3f4a1e)" role="img" aria-label="Hand stacking coins into rising piles"></div>
  <h4 class="news-title">NORVELL HUB COMPLETES $22,000,000 STRUCTURED DEBT INVESTMENT</h4>
  <p class="news-text">We have an extremely strong footprint in Europe, and we are now expanding aggressively in offering.</p>
  <div class="news-rule"></div>
  <div class="news-meta"><svg width="12" height="12"><rect x="1" y="2" width="10" height="9" fill="none" stroke="#888"/><rect x="1" y="2" width="10" height="3" fill="#888"/></svg>OCTOBER 19, 2016 &nbsp;&nbsp; <svg width="14" height="12"><path d="M2 10l10-8M4 11l9-7" stroke="#888" fill="none"/></svg>15</div>
</article>
<article class="news-card" style="left:765px">
  <div class="news-img" style="background:linear-gradient(135deg,#6b6f8a,#3a3d5c 55%,#8b8fa8)" role="img" aria-label="Business team in a meeting at a conference table"></div>
  <h4 class="news-title">CORVIX SEMICONDUCTOR ACQUIRED BY PEAKWAVE FOR $55,000,000</h4>
  <p class="news-text">Lumatrix, Inc., a leading supplier of advanced components for use in Cloud connectivity, data centers,</p>
  <div class="news-rule"></div>
  <div class="news-meta"><svg width="12" height="12"><rect x="1" y="2" width="10" height="9" fill="none" stroke="#888"/><rect x="1" y="2" width="10" height="3" fill="#888"/></svg>APRIL 30, 2018 &nbsp;&nbsp; <svg width="14" height="12"><path d="M2 10l10-8M4 11l9-7" stroke="#888" fill="none"/></svg>15</div>
</article>

<section class="ph cta" role="img" aria-label="Dim city skyline at dusk">
  <p class="cta-text">MAKE A DIFFERENCE WITH EXPERT TEAM</p>
  <div class="cta-btn">LET’S WORK TOGETHER</div>
</section>

<h2 class="section-title" style="top:3190px">OUR EXPERT TEAM</h2>

<div class="member" style="left:168px">
  <div class="avatar" role="img" aria-label="Portrait of the managing partner"></div>
  <p class="member-name">DANIEL FERROW</p>
  <p class="member-role">MANAGING PARTNER</p>
</div>
<div class="member" style="left:481px">
  <div class="avatar hover"><strong>TECHNOLOGY</strong><span>Samir Okafor leads technology investment origination and evaluation</span></div>
  <p class="member-name">SAMIR OKAFOR</p>
  <p class="member-role">MANAGING PARTNER</p>
</div>
<div class="member" style="left:794px">
  <div class="avatar" role="img" aria-label="Portrait of the partner"></div>
  <p class="member-name">TOM HADLEY</p>
  <p class="member-role">PARTNER</p>
</div>

<footer class="ph site-footer">
  <nav class="footer-nav"><span>Home</span><span>Strategy</span><span>About Us</span><span>Team</span><span>News</span><span>Contact</span><span>Investors</span></nav>
  <p class="copyright">© 2019 All Rights Reserved</p>
</footer>

</body>
</html>
```